Business Card for beauty technology startup

Design Glimora Business Card for a Beauty, based on the website identity and colors (https://www.glimora-example.com).
Glimora is a beauty tech startup that gathers helpful product info for beauty lovers and consumers (such as availability on stores, price range and product reviews) for makeup products. The card design must be young, colorful but clean, and very modern.

Target Market(s)

woman, 15-35

Industry/Entity Type

Cosmetics

Contact Information for Business Card

Full Name, address, phone

Font styles to use
Other font styles liked:
• Advent Pro

Colors
e34297
86cfc6
ffffff
5c5c5c
e8e8e8
e667a6
b2b2b2

Requirements
Must have
• One full colored side with a creative design and another with card info
• Use Color palette: #95C5C5 and/or #D38AA5
• Use fonts: Advent Pro
• Use website identity: https://www.glimora-example.com
Nice to have
• If needed extra font: Roboto

```html
<!DOCTYPE html>
<html lang="en">
<head>
<meta charset="utf-8">
<title>Glimora Business Card</title>
<link href="https://fonts.googleapis.com/css2?family=Advent+Pro:wght@200;300;400&family=Roboto:wght@400;500&family=Roboto+Condensed:wght@700&display=swap" rel="stylesheet">
<style>
  :root {
    --backdrop: #5b5855;
    --card-dark: #1b1b1d;
    --card-pink: #c38098;
    --accent-pink: #c98aa4;
    --soft-pink: #f2b5cd;
    --white: #ffffff;
    --rule: #d9d9d9;
  }
  * { margin: 0; padding: 0; box-sizing: border-box; }
  html, body { width: 1200px; height: 960px; overflow: hidden; }
  body { background: var(--backdrop); position: relative; font-family: "Roboto", sans-serif; }

  .card { position: absolute; width: 600px; height: 342px; border-radius: 18px; box-shadow: 0 8px 16px rgba(0,0,0,.35); }

  /* Info side */
  .card-info { left: 315px; top: 113px; background: var(--card-dark); color: var(--white); }
  .brand-lockup { position: absolute; right: 30px; top: 42px; display: flex; align-items: center; gap: 40px; }
  .brand-mark { width: 60px; height: 60px; border: 2px solid var(--accent-pink); border-radius: 50%; }
  .brand-name { font-family: "Advent Pro", sans-serif; font-weight: 300; font-size: 50px; letter-spacing: 5px; color: var(--accent-pink); line-height: 1; }

  .person-name { position: absolute; left: 26px; top: 158px; font-family: "Roboto Condensed", sans-serif; font-weight: 700; font-size: 23px; color: var(--accent-pink); }
  .person-title { position: absolute; left: 26px; top: 187px; font-size: 15px; font-weight: 500; }
  .divider { position: absolute; left: 26px; right: 30px; top: 211px; height: 1px; background: var(--rule); }

  .contact-list { position: absolute; left: 28px; top: 221px; list-style: none; font-size: 14px; line-height: 19.3px; }
  .contact-list li { display: flex; align-items: center; gap: 8px; }
  .contact-list svg { width: 13px; height: 13px; fill: var(--accent-pink); }

  .address { position: absolute; right: 30px; top: 229px; text-align: right; font-size: 14px; line-height: 19px; }
  .website { position: absolute; right: 30px; top: 279px; font-size: 14px; letter-spacing: 1px; }

  /* Brand side */
  .card-brand { left: 311px; top: 473px; background: var(--card-pink); text-align: center; }
  .brand-circle { position: absolute; left: 248px; top: 78px; width: 104px; height: 104px; border: 2px solid var(--soft-pink); border-radius: 50%; }
  .brand-title { position: absolute; left: 0; right: 0; top: 208px; font-family: "Advent Pro", sans-serif; font-weight: 300; font-size: 48px; letter-spacing: 6px; color: var(--soft-pink); line-height: 1; }
  .brand-url { position: absolute; left: 0; right: 0; top: 293px; font-size: 13px; letter-spacing: 4px; color: var(--soft-pink); }
</style>
</head>
<body>

<section class="card card-info">
  <div class="brand-lockup">
    <span class="brand-mark"></span>
    <span class="brand-name">GLIMORA</span>
  </div>

  <h1 class="person-name">CLARA MENDES</h1>
  <p class="person-title">CEO/FOUNDER</p>
  <div class="divider"></div>

  <ul class="contact-list">
    <li><svg viewBox="0 0 24 24"><path d="M6.6 10.8c1.4 2.8 3.8 5.1 6.6 6.6l2.2-2.2c.3-.3.7-.4 1-.2 1.1.4 2.3.6 3.6.6.6 0 1 .4 1 1V20c0 .6-.4 1-1 1C10.6 21 3 13.4 3 4c0-.6.4-1 1-1h3.5c.6 0 1 .4 1 1 0 1.3.2 2.5.6 3.6.1.3 0 .7-.2 1z"/></svg>555 218 4071</li>
    <li><svg viewBox="0 0 24 24"><path d="M7 1h10a2 2 0 0 1 2 2v18a2 2 0 0 1-2 2H7a2 2 0 0 1-2-2V3a2 2 0 0 1 2-2zm0 3v14h10V4z"/></svg>555 730 6192</li>
    <li><svg viewBox="0 0 24 24"><path d="M6 2h12v6H6zM3 9h18a2 2 0 0 1 2 2v7h-4v4H5v-4H1v-7a2 2 0 0 1 2-2zm4 7v4h10v-4z"/></svg>555 904 3385</li>
    <li><svg viewBox="0 0 24 24"><path d="M2 5h20v14H2zm2 2v.5l8 5 8-5V7z"/></svg>info@glimora-example.com</li>
  </ul>

  <address class="address" style="font-style:normal">214 Larkspur Court<br>Juneau, Alaska 99801</address>
  <p class="website">www.glimora-example.com</p>
</section>

<section class="card card-brand">
  <span class="brand-circle"></span>
  <h2 class="brand-title">GLIMORA</h2>
  <p class="brand-url">www.glimora-example.com</p>
</section>

</body>
</html>
```